Website for my photography business

I need a website for my photography business, Bram Kellet Photography. I need a website that has a landing page with a cover photo of each kind of photography I do. For example, Nature, Weddings, Portraits and Architecture. I want it so that when someone comes onto my website they have to choose which kind of photography page they want to visit. So if they click on the wedding photo it will open to a page with my wedding portfolio images and a contact me button. If they choose nature photography I want them to be redirected to an e-commerce section where they can purchase prints. Architecture and Portraits should open up to their respective portfolios with about me and contact info. I like this kind of format because I want people who come to my website for a specific type of photography to be able to be directed there easily without having to look at a mix of other kinds of photography. I will provide a few files to use as placeholders. I have already purchased the bramkelletphotography.example domain name. A Wix website would be great because I am most familiar with it but I am open to anything.

Industry/Entity Type

Photographer

Number of Pages Required

5+ page

Requirements
Must have
• Landing Page and e-commerce

```html
<!DOCTYPE html>
<html lang="en">
<head>
<meta charset="utf-8">
<title>Bram Kellet Photography</title>
<link rel="stylesheet" href="https://fonts.googleapis.com/css2?family=Poppins:wght@300;400;500&family=Courgette&display=swap">
<style>
  :root {
    --navy: #25285a;
    --ink: #0e1030;
    --accent: #fbb034;
    --accent-soft: rgba(251,176,52,.12);
    --muted: #555a66;
    --white: #ffffff;
  }
  * { box-sizing: border-box; margin: 0; padding: 0; }
  html, body { width: 1200px; height: 2656px; overflow: hidden; background: var(--white); }
  body { position: relative; font-family: "Poppins", sans-serif; color: var(--navy); }
  a { color: inherit; text-decoration: none; }
  .abs { position: absolute; }

  .brand { left: 80px; top: 50px; font-size: 26px; font-weight: 400; color: var(--navy); display: flex; align-items: center; gap: 12px; }
  .brand-dot { width: 12px; height: 12px; background: var(--accent); border-radius: 50%; }
  .main-nav { right: 78px; top: 36px; display: flex; gap: 30px; font-size: 14px; font-weight: 300; color: var(--muted); align-items: center; }
  .main-nav .current { color: var(--navy); position: relative; }
  .main-nav .current::after { content: ""; position: absolute; left: -2px; bottom: -5px; width: 22px; height: 2px; background: var(--accent); }

  .ornament-ring { left: 956px; top: 119px; width: 52px; height: 52px; background: var(--accent-soft); }
  .ornament-right { left: 1105px; top: 170px; width: 95px; height: 145px; background: linear-gradient(90deg, var(--accent-soft), rgba(251,176,52,.04)); }
  .ornament-left { left: 0; top: 428px; width: 80px; height: 140px; background: linear-gradient(90deg, rgba(251,176,52,.04), var(--accent-soft)); }

  .hero-lead { left: 80px; top: 188px; font-size: 82px; font-weight: 400; line-height: 1.1; color: var(--navy); }
  .hero-name { left: 80px; top: 290px; font-family: "Courgette", cursive; font-size: 88px; line-height: 1.15; color: var(--navy); white-space: nowrap; }

  .section-label { width: 1200px; left: 0; text-align: center; font-size: 14px; font-weight: 300; color: var(--muted); }

  .category { width: 511px; height: 386px; display: flex; align-items: center; justify-content: center; color: var(--white); font-size: 24px; font-weight: 400; }
  .cat-wedding { left: 77px; top: 502px; background: radial-gradient(ellipse at 55% 50%, #efe2cc 0%, #c9a77c 45%, #8e6a40 100%); }
  .cat-nature { left: 612px; top: 502px; background: radial-gradient(ellipse at 65% 35%, #6b5240 0%, #4a3a2e 50%, #847767 100%); }
  .cat-portraits { left: 77px; top: 911px; background: radial-gradient(ellipse at 55% 45%, #7a4630 0%, #3b1c12 55%, #1c0c08 100%); }
  .cat-architecture { left: 612px; top: 911px; background: linear-gradient(180deg, #4a5a64 0%, #2d3a40 45%, #4b2826 80%, #1f1a1c 100%); }

  .script-title { width: 1200px; left: 0; text-align: center; font-family: "Courgette", cursive; font-size: 46px; color: var(--navy); }

  .gallery-shot { width: 323px; height: 292px; top: 1486px; }
  .shot-1 { left: 94px; background: linear-gradient(180deg, #8a9a8e 0%, #c3b38a 45%, #8e7440 100%); }
  .shot-2 { left: 438px; background: linear-gradient(180deg, #d8d6dc 0%, #9a7a62 45%, #55612e 100%); }
  .shot-3 { left: 782px; background: linear-gradient(180deg, #2f4a34 0%, #5f6d58 45%, #c97a3a 65%, #eef2f6 100%); }
  .prints-link { width: 1200px; left: 0; top: 1797px; text-align: center; font-family: "Courgette", cursive; font-size: 17px; color: var(--accent); text-decoration: underline; }

  .cta-band { left: 0; top: 1901px; width: 1200px; height: 324px; background: linear-gradient(180deg, #3a3b3e 0%, #28292c 50%, #1b1c1f 100%); }
  .cta-title { width: 1200px; left: 0; top: 1982px; text-align: center; font-family: "Courgette", cursive; font-size: 40px; color: var(--white); }
  .cta-sub { width: 1200px; left: 0; top: 2044px; text-align: center; font-size: 14px; color: var(--white); }
  .cta-button { left: 510px; top: 2080px; width: 180px; height: 56px; border-radius: 4px; background: var(--accent); color: var(--white); font-family: "Courgette", cursive; font-size: 20px; display: flex; align-items: center; justify-content: center; }

  .site-footer { left: 0; top: 2225px; width: 1200px; height: 431px; background: var(--ink); color: var(--white); }
  .footer-col { top: 42px; width: 240px; text-align: center; }
  .footer-col h3 { font-family: "Courgette", cursive; font-weight: 400; font-size: 22px; margin-bottom: 22px; }
  .footer-col li { list-style: none; font-size: 14px; font-weight: 300; line-height: 27px; }
  .col-sitemap { left: 72px; }
  .col-account { left: 343px; }
  .col-photo { left: 611px; }
  .col-news { left: 882px; }
  .col-news p { font-size: 14px; font-weight: 300; line-height: 27px; }
  .email-field { margin: 12px auto 0; width: 245px; height: 46px; background: var(--white); border-radius: 4px; color: #777; font-size: 13px; text-align: left; padding: 14px 17px; }
  .subscribe { margin: 8px auto 0; width: 245px; height: 46px; background: var(--accent); border-radius: 4px; font-family: "Courgette", cursive; font-size: 20px; display: flex; align-items: center; justify-content: center; }
  .footer-rule { left: 77px; top: 282px; width: 1046px; border-top: 1px dotted rgba(255,255,255,.35); }
  .copyright { width: 1200px; left: 0; top: 330px; text-align: center; font-size: 14px; font-weight: 300; }
  .social { left: 555px; top: 358px; display: flex; gap: 6px; }
  .social a { width: 46px; height: 46px; border: 1.5px solid var(--accent); border-radius: 50%; display: flex; align-items: center; justify-content: center; font-size: 10px; font-weight: 400; color: var(--accent); }
</style>
</head>
<body>
  <div class="abs brand"><span class="brand-dot"></span>Bram Kellet Photography</div>
  <nav class="abs main-nav">
    <a class="current" href="#">Home</a>
    <a href="#">About Me</a>
    <a href="#">Photography</a>
    <a href="#">Contact</a>
    <svg width="20" height="20" viewBox="0 0 20 20" fill="none" stroke="#25285a" stroke-width="1.5" aria-label="Cart"><path d="M1 2h3l2.5 10h10l2-7H5"/><circle cx="8" cy="16.5" r="1.5"/><circle cx="15" cy="16.5" r="1.5"/></svg>
  </nav>

  <div class="abs ornament-ring" role="img" aria-label="Decorative orange ring ornament"></div>
  <div class="abs ornament-right" role="img" aria-label="Decorative orange dot pattern"></div>
  <div class="abs ornament-left" role="img" aria-label="Decorative orange dot pattern"></div>

  <h1 class="abs hero-lead">Welcome to</h1>
  <div class="abs hero-name">Bram Kellet Photography</div>

  <p class="abs section-label" style="top:458px">Browse by Categories</p>

  <a class="abs category cat-wedding" href="#" role="img" aria-label="Wedding rings on a lace pillow held in a hand">Wedding</a>
  <a class="abs category cat-nature" href="#" role="img" aria-label="Brown bear among rocks">Nature</a>
  <a class="abs category cat-portraits" href="#" role="img" aria-label="Close-up portrait of a woman">Portraits</a>
  <a class="abs category cat-architecture" href="#" role="img" aria-label="Round tower seen from below with a plane overhead">Architecture</a>

  <h2 class="abs script-title" style="top:1370px">latest Advanture</h2>
  <p class="abs section-label" style="top:1434px">Nature Photography</p>

  <div class="abs gallery-shot shot-1" role="img" aria-label="Photographer with tripod on a misty hillside"></div>
  <div class="abs gallery-shot shot-2" role="img" aria-label="Stone castle tower on a mossy cliff"></div>
  <div class="abs gallery-shot shot-3" role="img" aria-label="Red fox sitting in snow under pine trees"></div>
  <a class="abs prints-link" href="#">Purchase prints</a>

  <div class="abs cta-band" role="img" aria-label="Misty lake with wooden pier posts and a gull"></div>
  <h2 class="abs cta-title">let's Create Some Magic</h2>
  <p class="abs cta-sub">Bram Kellet Photography</p>
  <a class="abs cta-button" href="#">Contact Us</a>

  <footer class="abs site-footer">
    <div class="abs footer-col col-sitemap">
      <h3>Sitemap</h3>
      <ul><li>Home</li><li>About Me</li><li>Photography</li><li>Contact Us</li></ul>
    </div>
    <div class="abs footer-col col-account">
      <h3>My Account</h3>
      <ul><li>My Account</li><li>Oredr History</li><li>Wishlist</li><li>Shopping Guide</li><li>Contact Us</li></ul>
    </div>
    <div class="abs footer-col col-photo">
      <h3>Photography</h3>
      <ul><li>Nature</li><li>Wedding</li><li>Portraits</li><li>Architecture</li></ul>
    </div>
    <div class="abs footer-col col-news">
      <h3>Newsletter</h3>
      <p>Receive our exclusive update<br>for signup!</p>
      <div class="email-field">Enter Email *</div>
      <div class="subscribe">Subscribe</div>
    </div>
    <div class="abs footer-rule"></div>
    <p class="abs copyright">©Bram Kellet - 2020 All rights reserved.</p>
    <div class="abs social" aria-label="Social links"><a href="#">Netly</a><a href="#">Pixly</a></div>
  </footer>
</body>
</html>
```